Accountability Project Graphics

I want to create 10 social media graphics (new Instagram size 4:5 (1080 x 1350 pixels) focusing on our Quilvo Accountability App, using any of the 3 pictures attached. Use the attached pics only, NO RANDOM STOCK PHOTOGRAPHY. For the color scheme, use the landing page colors/fonts (attached).
You can add any of the 3 photos attached but I mainly need BOLD text that includes these headlines and sub-headlines on them.
Please NOTE for all the headlines below, also add this sub-headline on each graphic:
Stay Consistent with RT in Your Pocket!
Here are the headlines:
• Stop Starting Over Every Monday
• You don't need more willpower. You need more support
• Built for women who are tired of doing this alone
• When Motivation Fades, RT Checks In
• The Support System You've Been Missing
• Support When Motivation Disappears
• What if RT Checked in Every Day?
• The Missing Piece Isn't Another Diet
• Eat the food you love. Stay accountable every day.
• One Bad Meal Doesn't Mean You Failed
women over 40 trying to lose weight

```html
<!DOCTYPE html>
<html lang="en">
<head>
<meta charset="utf-8">
<title>Accountability App Social Graphics</title>
<link rel="stylesheet" href="https://fonts.googleapis.com/css2?family=Della+Respira&family=Poppins:ital,wght@1,700&display=swap">
<style>
  :root {
    --canvas: #e6e6e6;
    --rose: #c55a7b;
    --rose-deep: #b24a6c;
    --plum: #3a2145;
    --plum-soft: #4e2c55;
    --blush: #fcd6e3;
    --blush-pale: #fde9ef;
    --white: #ffffff;
    --photo-warm-a: #e8c9b6;
    --photo-mauve-a: #dcb0d8;
    --photo-mauve-b: #a2637f;
    --photo-cool-a: #b8bec4;
    --photo-cool-b: #3b3540;
  }
  * { box-sizing: border-box; margin: 0; padding: 0; }
  html, body { width: 1200px; height: 2785px; overflow: hidden; background: var(--canvas); }
  .board { position: relative; width: 1200px; height: 2785px; }

  .post {
    position: absolute; width: 370px; height: 464px; overflow: hidden;
    font-family: "Della Respira", Georgia, serif;
  }
  .col-a { left: 222px; } .col-b { left: 608px; }
  .row-1 { top: 197px; } .row-2 { top: 679px; } .row-3 { top: 1161px; }
  .row-4 { top: 1643px; } .row-5 { top: 2125px; }

  .tagline {
    position: absolute; left: 0; bottom: 0; width: 100%; height: 46px;
    display: flex; align-items: center; justify-content: center;
    font-family: "Poppins", Arial, sans-serif; font-weight: 700; font-style: italic;
    font-size: 15.5px; color: var(--white); letter-spacing: -0.1px;
  }
  .tagline.on-rose { background: var(--rose); }
  .tagline.on-plum { background: var(--plum); }

  .photo { position: absolute; }
  .photo.hug { background: linear-gradient(135deg, var(--photo-mauve-a), #e7a8c3 45%, var(--photo-mauve-b)); }
  .photo.duo { background: linear-gradient(180deg, var(--photo-warm-a), #b79a8e 50%, #35406a); }
  .photo.solo { background: linear-gradient(180deg, var(--photo-cool-a), #6e6470 40%, var(--photo-cool-b)); }

  .headline {
    position: absolute; color: var(--white); text-align: center; line-height: 1.08;
    font-weight: 400; letter-spacing: 0.6px;
  }
  .headline.dark { color: var(--plum); }

  /* 1 */
  .stop-monday { background: var(--white); }
  .stop-monday .photo { left: 0; top: 0; width: 370px; height: 327px; }
  .stop-monday .headline { left: 0; top: 337px; width: 100%; font-size: 31px; }

  /* 2 */
  .willpower { background: var(--rose); }
  .willpower .photo { left: 0; top: 120px; width: 370px; height: 298px; }
  .willpower .wave { position: absolute; left: 0; top: 100px; width: 370px; height: 80px; }
  .willpower .headline { left: 0; top: 12px; width: 100%; font-size: 27px; line-height: 1.2; letter-spacing: 0.3px; }

  /* 3 */
  .built-for { background: linear-gradient(180deg, var(--rose), var(--rose-deep)); }
  .built-for .photo { right: 0; top: 0; width: 172px; height: 418px; }
  .built-for .headline { left: 20px; top: 38px; text-align: left; font-size: 35px; line-height: 1.2; letter-spacing: 0.3px; }

  /* 4 */
  .motivation-fades { background: var(--blush); }
  .motivation-fades .headline { left: 0; top: 30px; width: 100%; font-size: 30px; }
  .motivation-fades .photo { left: 0; top: 135px; width: 370px; height: 283px; border-radius: 185px 185px 0 0; }

  /* 5 */
  .support-system { background: var(--white); }
  .support-system .photo { left: 0; top: 0; width: 370px; height: 300px; border-top-right-radius: 150px; }
  .support-system .panel { position: absolute; left: 0; top: 175px; width: 370px; height: 243px; background: var(--plum); border-radius: 130px 0 130px 0; }
  .support-system .headline { left: 0; top: 235px; width: 100%; font-size: 38px; }

  /* 6 */
  .checked-circle { background: var(--blush-pale); }
  .checked-circle .card { position: absolute; left: 15px; top: 40px; width: 342px; height: 343px; background: var(--rose); border-radius: 6px; }
  .checked-circle .photo { left: 15px; top: 40px; width: 342px; height: 343px; border-radius: 50%; }
  .checked-circle .shade { position: absolute; left: 15px; top: 40px; width: 342px; height: 343px; border-radius: 50%; background: linear-gradient(180deg, transparent 58%, var(--plum-soft) 70%, var(--plum) 100%); }
  .checked-circle .headline { left: 0; top: 290px; width: 100%; font-size: 25px; }

  /* 7 */
  .motivation-gone { background: var(--white); }
  .motivation-gone .photo { left: 14px; top: 9px; width: 346px; height: 409px; }
  .motivation-gone .arch { position: absolute; left: 14px; top: 303px; width: 346px; height: 130px; background: var(--plum); border-radius: 173px 173px 0 0 / 80px 80px 0 0; opacity: 0.95; }
  .motivation-gone .headline { left: 0; top: 344px; width: 100%; font-size: 25px; }

  /* 8 */
  .missing-piece .photo { left: 0; top: 0; width: 370px; height: 418px; }
  .missing-piece .banner { position: absolute; left: 0; top: 0; width: 370px; height: 122px; background: var(--rose); clip-path: polygon(0 0, 100% 0, 100% 55%, 50% 100%, 0 55%); }
  .missing-piece .headline { left: 0; top: 14px; width: 100%; font-size: 25px; }

  /* 9 */
  .bad-meal .photo { left: 0; top: 0; width: 370px; height: 418px; }
  .bad-meal .fade { position: absolute; left: 0; top: 0; width: 370px; height: 418px; background: linear-gradient(180deg, transparent 62%, var(--rose) 88%); }
  .bad-meal .headline { left: 0; top: 352px; width: 100%; font-size: 26px; }

  /* 10 */
  .food-you-love .photo { left: 0; top: 0; width: 370px; height: 418px; }
  .food-you-love .fade { position: absolute; left: 0; top: 0; width: 370px; height: 418px; background: linear-gradient(180deg, transparent 52%, var(--plum) 82%); }
  .food-you-love .headline { left: 0; top: 328px; width: 100%; font-size: 26px; }
</style>
</head>
<body>
<main class="board">

  <section class="post stop-monday col-a row-1">
    <div class="photo hug" role="img" aria-label="Photo of two women embracing and laughing in a store"></div>
    <h2 class="headline dark">Stop Starting<br>Over Every Monday</h2>
    <p class="tagline on-rose">Stay Consistent with RT in Your Pocket!</p>
  </section>

  <section class="post willpower col-b row-1">
    <div class="photo duo" role="img" aria-label="Photo of two women standing together smiling"></div>
    <svg class="wave" viewBox="0 0 370 80" preserveAspectRatio="none" aria-hidden="true">
      <path d="M0 0 H370 V30 C300 70 200 62 120 40 C70 28 30 22 0 24 Z" fill="var(--rose)"/>
      <path d="M370 30 C330 58 290 68 240 66 C300 72 340 62 370 48 Z" fill="var(--white)"/>
      <path d="M370 48 C340 62 300 72 240 66 C300 80 340 74 370 62 Z" fill="var(--rose-deep)"/>
    </svg>
    <h2 class="headline">You Don't<br>Need More Willpower.<br>You Need More Support</h2>
    <p class="tagline on-plum">Stay Consistent with RT in Your Pocket!</p>
  </section>

  <section class="post built-for col-a row-2">
    <div class="photo solo" role="img" aria-label="Photo of a smiling woman in a black outfit posing by a pool table"></div>
    <h2 class="headline">Built<br>For<br>Women<br>Who Are<br>Tired Of<br>Doing<br>This<br>Alone</h2>
    <p class="tagline on-plum">Stay Consistent with RT in Your Pocket!</p>
  </section>

  <section class="post motivation-fades col-b row-2">
    <h2 class="headline dark">When Motivation<br>Fades, RT Checks In</h2>
    <div class="photo hug" role="img" aria-label="Photo of two women embracing and laughing"></div>
    <p class="tagline on-rose">Stay Consistent with RT in Your Pocket!</p>
  </section>

  <section class="post support-system col-a row-3">
    <div class="photo duo" role="img" aria-label="Photo of two women standing together laughing"></div>
    <div class="panel"></div>
    <h2 class="headline">The Support<br>System You've<br>Been Missing</h2>
    <p class="tagline on-rose">Stay Consistent with RT in Your Pocket!</p>
  </section>

  <section class="post checked-circle col-b row-3">
    <div class="card"></div>
    <div class="photo solo" role="img" aria-label="Photo of a smiling woman in a black outfit"></div>
    <div class="shade"></div>
    <h2 class="headline">What If RT Checked<br>In Every Day?</h2>
    <p class="tagline on-plum">Stay Consistent with RT in Your Pocket!</p>
  </section>

  <section class="post motivation-gone col-a row-4">
    <div class="photo solo" role="img" aria-label="Photo of a smiling woman in a black outfit beside a pool table"></div>
    <div class="arch"></div>
    <h2 class="headline">Support When<br>Motivation Disappears</h2>
    <p class="tagline on-rose">Stay Consistent with RT in Your Pocket!</p>
  </section>

  <section class="post missing-piece col-b row-4">
    <div class="photo duo" role="img" aria-label="Photo of two women standing together laughing"></div>
    <div class="banner"></div>
    <h2 class="headline">The Missing Piece Isn't<br>Another Diet</h2>
    <p class="tagline on-plum">Stay Consistent with RT in Your Pocket!</p>
  </section>

  <section class="post bad-meal col-a row-5">
    <div class="photo solo" role="img" aria-label="Photo of a smiling woman in a black outfit"></div>
    <div class="fade"></div>
    <h2 class="headline">One Bad Meal<br>Doesn’t Mean You Failed</h2>
    <p class="tagline on-plum">Stay Consistent with RT in Your Pocket!</p>
  </section>

  <section class="post food-you-love col-b row-5">
    <div class="photo hug" role="img" aria-label="Photo of two women embracing and laughing"></div>
    <div class="fade"></div>
    <h2 class="headline">Eat the food you love.<br>Stay accountable<br>every day.</h2>
    <p class="tagline on-rose">Stay Consistent with RT in Your Pocket!</p>
  </section>

</main>
</body>
</html>
```